Locksmith Business Cards

My father-in-law is in need of new business cards for his locksmith business and I need to impress him. Kindly help me out!

You can see the previous business card attached. It is a family run business in North Wales.

No individual names on the cards.

Key Things to Feature:
- The words "Prompt", "Local", "Reliable" (as you can see under the logo on the website)
- 24h Emergency Service
- Covering All of North Wales, the Wirral and Chester
- The color blue
- A key or a lock would be interesting (similar to the ones that come up when you google locksmith business card)

Optional (only if design includes bullet points, like the example below):
https://imgvaultcdn.net/samples/208314/55172/55172_3904821_208314_image.jpg
- Residential / Commercial / Automotive
- Alarms & Cameras
- Key Cutting & Safes

https://www.brynhafod-locksmiths.co.uk/

Industry/Entity Type

Locksmith

Contact Information for Business Card

01632 960 418
07700 900 362
brynhafodlocksmiths@mailvane.com
Brynhafod Locksmiths, The Willow Barn, 7 Tannery Rd., Llandudno LL99 4QX
www.brynhafod-locksmiths.co.uk

Requirements
Must have
• - The words "Prompt", "Local", "Reliable" (as you can see under the logo on the website)
• - 24h Emergency Service
• - Covering All of North Wales, the Wirral and Chester
Nice to have
• - A key or a lock would be interesting (similar to the ones that come up when you google locksmith business card)

```html
<!DOCTYPE html>
<html lang="en">
<head>
<meta charset="utf-8">
<title>Brynhafod Locksmiths – Business Card</title>
<link rel="stylesheet" href="https://fonts.googleapis.com/css2?family=Oswald:wght@400;500;600&display=swap">
<style>
  :root {
    --navy: #1f2a6b;
    --navy-deep: #1b2462;
    --blue: #4a5ca8;
    --blue-band: #2e3c86;
    --ink: #3a3a3a;
    --paper: #ffffff;
    --backdrop: #e4e4e6;
    --rule: #e2e2e2;
  }
  * { box-sizing: border-box; margin: 0; padding: 0; }
  html, body { width: 1200px; height: 782px; overflow: hidden; }
  body {
    background: var(--backdrop);
    font-family: "Oswald", sans-serif;
    display: flex;
    align-items: center;
    justify-content: center;
    gap: 40px;
  }
  .card {
    position: relative;
    width: 540px;
    height: 309px;
    overflow: hidden;
    box-shadow: 0 6px 18px rgba(0,0,0,0.18);
  }

  /* Front */
  .card-front { background: var(--paper); }
  .brand {
    position: absolute;
    left: 30px;
    top: 78px;
    width: 220px;
  }
  .brand-name {
    display: flex;
    align-items: center;
    gap: 10px;
  }
  .brand-mark {
    width: 34px;
    height: 34px;
    background: var(--navy);
    flex: none;
  }
  .brand-title {
    font-weight: 600;
    font-size: 26px;
    line-height: 1;
    color: var(--navy);
    text-transform: uppercase;
  }
  .tagline {
    margin-top: 8px;
    margin-left: 44px;
    font-size: 12px;
    font-weight: 600;
    letter-spacing: 0.5px;
    color: var(--navy);
  }
  .divider {
    position: absolute;
    left: 262px;
    top: 70px;
    width: 1px;
    height: 130px;
    background: var(--rule);
  }
  .contact {
    position: absolute;
    left: 278px;
    top: 66px;
    font-size: 14px;
    font-weight: 500;
    color: var(--ink);
    line-height: 1.3;
    list-style: none;
  }
  .contact li { display: flex; align-items: center; gap: 6px; }
  .contact .address { display: block; padding-left: 20px; margin-bottom: 2px; }
  .contact svg { width: 14px; height: 14px; flex: none; fill: var(--navy); }
  .service {
    position: absolute;
    left: 0;
    right: 0;
    top: 222px;
    text-align: center;
    padding-right: 40px;
  }
  .service-emergency {
    font-size: 15px;
    font-weight: 600;
    color: var(--navy);
    line-height: 1.2;
  }
  .service-area {
    font-size: 15px;
    font-weight: 500;
    color: var(--blue);
    line-height: 1.2;
  }
  .band {
    position: absolute;
    left: 0; right: 0; bottom: 0;
    height: 20px;
    display: flex;
  }
  .band-left { width: 55%; background: var(--navy); }
  .band-gap { width: 5px; background: var(--paper); }
  .band-right { flex: 1; background: var(--blue); }

  /* Back */
  .card-back {
    background: var(--navy-deep);
  }
  .back-pattern {
    position: absolute;
    inset: 0;
    background: linear-gradient(180deg, #2b3680 0%, #26307a 30%, #1e2767 30%, #1d2563 70%, #222b6d 70%, #222b6d 100%);
  }
  .services {
    position: relative;
    height: 100%;
    display: flex;
    flex-direction: column;
    align-items: center;
    justify-content: center;
    color: #fff;
    font-size: 16px;
    font-weight: 500;
    line-height: 1.3;
    list-style: none;
    text-align: center;
  }
</style>
</head>
<body>
  <section class="card card-front" aria-label="Business card front">
    <div class="brand">
      <div class="brand-name">
        <span class="brand-mark"></span>
        <span class="brand-title">Brynhafod Locksmiths</span>
      </div>
      <p class="tagline">Prompt. Local. Reliable</p>
    </div>
    <div class="divider"></div>
    <ul class="contact">
      <li class="address">Brynhafod Locksmiths,<br>The Willow Barn, 7 Tannery<br>Rd., Llandudno LL99 4QX</li>
      <li><svg viewBox="0 0 16 16"><path d="M2 5c0-2 2-3 6-3s6 1 6 3v1h-3V5H5v1H2z M4 7h8l2 6H2z"/></svg>01632 960 418</li>
      <li><svg viewBox="0 0 16 16"><path d="M4 1h8v14H4z M5 3v9h6V3z"/></svg>07700 900 362</li>
      <li><svg viewBox="0 0 16 16"><path d="M1 3h14v10H1z M2 4l6 5 6-5" stroke="#fff" stroke-width="1.2"/></svg>brynhafodlocksmiths@mailvane.com</li>
      <li><svg viewBox="0 0 16 16"><circle cx="8" cy="8" r="7"/><path d="M1 8h14 M8 1v14" stroke="#fff" stroke-width="1"/></svg>www.brynhafod-locksmiths.co.uk</li>
    </ul>
    <div class="service">
      <p class="service-emergency">24h Emergency Service</p>
      <p class="service-area">Covering All of North Wales, the Wirral and Chester</p>
    </div>
    <div class="band">
      <span class="band-left"></span>
      <span class="band-gap"></span>
      <span class="band-right"></span>
    </div>
  </section>

  <section class="card card-back" aria-label="Business card back">
    <div class="back-pattern" role="img" aria-label="Faint repeating pattern of padlock symbols on deep blue"></div>
    <ul class="services">
      <li>Residential / Commercial / Automotive</li>
      <li>Alarms &amp; Cameras</li>
      <li>Key Cutting &amp; Safes</li>
    </ul>
  </section>
</body>
</html>
```